Internal Office Slogans / Motto / Vision Statements

Hi. We would like to put up some posters around the office with quotations such as -
-”Do what you do so well that they will want to see it again and bring their friends.”- Hollis Brandt
-Make your customers feel heard and understood. Make your customers feel respected and liked. Make your customers feel appreciated and helped. Understand that you can do none of these things unless you are sincere about them.
Terrence Oakley
- It’s a very predictable and satisfying phenomenon: whenever we get better, our customers do too.
Cal Pruett
-Catch people in the act of performing extraordinary customer service. Treat them like heroes. Tell their stories, far and wide.
Ned Farraday

The purpose of the posters is to reiterate our culture and vision within the organisation. They should be clean, crisp and eye catching, not gaudy or bright. Professional, bold and strong.

The company website and logo is at http://www.nexoraweb.com.au
Print size will be A1

Thanks for participating & looking forward to seeing your great work.
Updates

Hi All. . 

So to reiterate we are looking for one background design to be used for multiple quotes...  The list of quotes are as follows: 

Support and or Sales Office

 

Make your customers feel heard and understood.Make your customers feel respected and liked. Make your customers feelappreciated and helped. Understand that you can do none of these things unlessyou are sincere about them.

Terrence Oakley

 

Nothing liberates our greatness like the desireto help, the desire to serve

Dorothea Quill

 

It’s a very predictable and satisfying phenomenon:whenever we get better, our customers do too.

Cal Pruett

 

Success means we go to sleep at night knowingthat our talents and abilities were used in a way that served others.

Dorothea Quill.

 

The sole purpose of business is to create, serveand satisfy a customer, from beginning to end – and that’s everyone’s job.

Ned Farraday

 

We don’t celebrate closing a sale, we celebrateopening a relationship.

Rosalind Hext

I will never make you a promise – unless I giveyou a plan and procedure to make that promise possible.

Bo Tennant

 

Customers feel we take them for granted; onlyshow interest when we want an order; lavish our time on prospects; communicatemainly by invoice; are fixated on big accounts; drop them like hot potatoesonce we have the order; don’t follow through on promises; and satisfy our ownbureaucracy rather than their needs. We can do better than that, much better.

Alan P Merrow.

 

 

General and public area

 

Catch people in the act of performingextraordinary customer service. Treat them like heroes. Tell their stories, farand wide.

Ned Farraday

 

 

We see our customers as invited guests to aparty, and we are the hosts. It’s our job every day to make every importantaspect of the customer experience a little bit better." Carl Voight - Founder andCEO of Halverin

 

"If you do build a great experience,customers tell each other about that. Word of mouth is verypowerful."  Carl Voight

 

It's not a faithin technology. It's faith in people. Rick Palmer

 

“Being the richest man in the cemetery doesn’tmatter to me … Going to bed at night saying we’ve done something wonderful…that’s what matters to me.” Rick Palmer

 

The customer experience is the next competitivebattleground. Lance Morrow, CIO, Vantor Computers

 

”Do what you do so well that they will want tosee it again and bring their friends.”- Hollis Brandt

In the world of internet customer service, it isimportant to remember your competitor is only a mouse click away. FrankHolden (not sure who he is but like the quote).

The customer is why you go to work. If they goaway, you do, too. Peter Lindqvist (?)

 

MaybeSome for Sales or Build Team:

Quality is remembered long after the price is forgotten. Marzetti Family Slogan

```html
<!DOCTYPE html>
<html lang="en">
<head>
<meta charset="utf-8">
<title>Customer Service Poster – Terrence Oakley</title>
<link rel="stylesheet" href="https://fonts.googleapis.com/css2?family=Saira+Extra+Condensed:wght@500&family=Pinyon+Script&display=swap">
<style>
  :root {
    --bg-center: #3b3b3b;
    --bg-mid: #262626;
    --bg-edge: #101010;
    --quote-ink: #e7e5e3;
    --author-ink: #6f86e0;
  }
  html, body {
    margin: 0;
    padding: 0;
    width: 850px;
    height: 1200px;
    overflow: hidden;
    background: var(--bg-edge);
  }
  .poster {
    position: relative;
    width: 850px;
    height: 1200px;
    background: radial-gradient(ellipse 75% 60% at 50% 45%, var(--bg-center) 0%, var(--bg-mid) 55%, var(--bg-edge) 100%);
  }
  .poster-art {
    position: absolute;
    inset: 0;
    width: 850px;
    height: 1200px;
  }
  .quote-line {
    font-family: "Saira Extra Condensed", "Arial Narrow", sans-serif;
    font-weight: 500;
    fill: var(--quote-ink);
    text-transform: uppercase;
  }
  .quote-author {
    font-family: "Pinyon Script", cursive;
    fill: var(--author-ink);
  }
</style>
</head>
<body>
  <main class="poster">
    <svg class="poster-art" viewBox="0 0 850 1200" xmlns="http://www.w3.org/2000/svg" role="img" aria-label="Make your customers feel heard and understood. Make your customers feel respected and liked. Make your customers feel appreciated and helped. Understand that you can do none of these things unless you are sincere about them. Terrence Oakley">
      <g class="quote">
        <text class="quote-line" x="86" y="164" font-size="75" textLength="537" lengthAdjust="spacingAndGlyphs">Make your customers</text>
        <text class="quote-line" x="86" y="248" font-size="65" textLength="702" lengthAdjust="spacingAndGlyphs">Feel heard and understood.</text>
        <text class="quote-line" x="86" y="331" font-size="68" textLength="653" lengthAdjust="spacingAndGlyphs">Make your customers feel</text>
        <text class="quote-line" x="86" y="420" font-size="100" textLength="702" lengthAdjust="spacingAndGlyphs">Respected and liked.</text>
        <text class="quote-line" x="86" y="484" font-size="55" textLength="519" lengthAdjust="spacingAndGlyphs">Make your customers feel</text>
        <text class="quote-line" x="86" y="567" font-size="68" textLength="603" lengthAdjust="spacingAndGlyphs">Appreciated and helped.</text>
        <text class="quote-line" x="86" y="623" font-size="58" textLength="322" lengthAdjust="spacingAndGlyphs">Understand that</text>
        <text class="quote-line" x="86" y="709" font-size="79" textLength="656" lengthAdjust="spacingAndGlyphs">You can do none of these</text>
        <text class="quote-line" x="86" y="785" font-size="72" textLength="515" lengthAdjust="spacingAndGlyphs">Things unless you are</text>
        <text class="quote-line" x="86" y="891" font-size="115" textLength="692" lengthAdjust="spacingAndGlyphs">Sincere about them.</text>
      </g>
      <text class="quote-author" x="797" y="1018" font-size="48" text-anchor="end">Terrence Oakley</text>
    </svg>
  </main>
</body>
</html>
```